Prosperity Pathway Basics PowerPoint

Please edit the following attached PowerPoint entitled workshop. Use the other attached PDF "TerraVesta Northern California Value Proposition" as a reference for the design and color I would like.

```html
<!DOCTYPE html>
<html lang="en">
<head>
<meta charset="utf-8">
<title>Prosperity Pathway Basics – Slide Overview</title>
<link href="https://fonts.googleapis.com/css2?family=Poppins:wght@400;500;600;700&display=swap" rel="stylesheet">
<style>
:root{
  --board:#b3b3b3;
  --navy:#062e74;
  --navy-deep:#0a2a6b;
  --royal:#0f44b0;
  --sky:#9fd3ee;
  --sky-pale:#eaf5fc;
  --ink:#2b2f3a;
  --muted:#5c6270;
  --white:#ffffff;
}
*{box-sizing:border-box;margin:0;padding:0}
html,body{width:1032px;height:1200px;overflow:hidden;background:var(--board)}
body{position:relative;font-family:"Poppins",sans-serif;color:var(--ink)}
.slide{position:absolute;width:764px;height:429px;background:var(--white);overflow:hidden;transform:scale(.5794);transform-origin:0 0}
.col-l{left:40.6px}.col-r{left:537.1px}
.row-1{top:43.5px}.row-2{top:329.1px}.row-3{top:614.2px}.row-4{top:899.8px}
.abs{position:absolute}
.header-shape{position:absolute;left:0;top:0}
.slide-title{position:absolute;left:35px;top:4px;color:var(--white);font-weight:700;font-size:25px;line-height:38px}
.footer{position:absolute;left:0;bottom:0;width:100%;height:17px;background:var(--sky);font-size:7.5px;color:var(--navy)}
.footer span{position:absolute;top:3px}
.footer .page{left:33px;font-weight:700}
.footer .rights{left:300px}
.footer .site{left:627px;display:flex;align-items:center;gap:4px}
.photo{position:absolute}
.bullets{list-style:none}
.bullets li{display:flex;align-items:center;gap:6px;font-size:10px;color:var(--muted)}
.tick{width:9px;height:9px;flex:none}
/* title slide */
.cover,.closing{background:linear-gradient(135deg,#1346b4 0%,#0c3a9c 55%,#0a2f85 100%)}
.cover-brand{position:absolute;left:0;width:100%;text-align:center;color:var(--white)}
.brand-name{top:138px;font-size:32px;font-weight:500;display:flex;justify-content:center;align-items:center;gap:8px}
.brand-dot{width:12px;height:12px;border-radius:50%;background:var(--white)}
.brand-region{top:178px;font-size:14px}
.cover-tag{top:214px;font-size:12.5px;font-weight:600}
.cover-btn{position:absolute;left:293px;top:256px;width:177px;height:29px;border-radius:15px;background:var(--sky);color:var(--navy);font-size:12px;font-weight:500;text-align:center;line-height:29px}
/* slide 2 */
.label{font-size:11px;font-weight:500;color:var(--ink)}
.note{font-size:10px;color:var(--navy)}
/* slide 3 */
.card{position:absolute;top:96px;width:322px;height:279px;background:var(--white);box-shadow:0 1px 6px rgba(0,0,0,.15)}
.card-band{position:absolute;left:0;top:0;width:100%;height:100px;background:var(--sky)}
.card .photo{left:20px;top:20px;width:283px;height:194px;border:2px solid var(--white)}
.card-title{position:absolute;top:230px;width:100%;text-align:center;font-size:12px;font-weight:500}
.card-sub{position:absolute;top:251px;width:100%;text-align:center;font-size:9.5px;color:var(--muted)}
/* slide 4 */
.logo-box{position:absolute;left:199px;top:95px;width:183px;height:70px;background:var(--navy);color:var(--white);text-align:center;box-shadow:0 2px 6px rgba(0,0,0,.25)}
.logo-box .name{margin-top:11px;font-size:22px;font-weight:500;display:flex;justify-content:center;align-items:center;gap:6px}
.logo-box .name i{width:8px;height:8px;border-radius:50%;background:var(--white)}
.logo-box .region{font-size:10px}
.body-copy{font-size:10.5px;line-height:18px;color:var(--ink)}
.emph{font-size:12.5px;font-weight:600;color:var(--navy)}
/* slide 5 */
.efficiency-copy{position:absolute;left:34px;top:155px;width:300px;font-size:10.5px;line-height:20px;color:var(--muted)}
.efficiency-copy p+p{margin-top:6px}
/* slide 7 */
.strategy-table{position:absolute;left:95px;top:89px;width:575px;border-collapse:collapse}
.strategy-table th{background:var(--navy);color:var(--white);font-size:11.5px;font-weight:600;height:43px;text-align:left;padding-left:30px}
.strategy-table th.eff{width:112px;padding:0;text-align:center;border-left:2px solid var(--white)}
.strategy-table td{background:var(--sky-pale);height:60px;font-size:9.5px;padding-left:27px;border-top:1px solid #d8e6f1}
.strategy-table td.eff{background:var(--sky);padding:0;border-left:2px solid var(--white);border-top:none}
.thanks{position:absolute;top:160px;width:100%;text-align:center;color:var(--white);font-size:36px;font-weight:700}
</style>
</head>
<body>

<!-- 01 Cover -->
<section class="slide cover col-l row-1">
  <div class="photo" role="img" aria-label="Team of professionals joining hands over a table, tinted blue" style="inset:0;background:radial-gradient(ellipse at 30% 60%,rgba(60,110,210,.45),transparent 60%),radial-gradient(ellipse at 80% 30%,rgba(40,90,190,.35),transparent 55%)"></div>
  <div class="cover-brand brand-name"><span class="brand-dot"></span>TerraVesta</div>
  <div class="cover-brand brand-region">Northern California</div>
  <div class="cover-brand cover-tag">SERVING OUR COMMUNITY FOR 165 YEARS</div>
  <div class="cover-btn">www.terravesta.com</div>
</section>

<!-- 02 Your Money -->
<section class="slide col-r row-1">
  <svg class="header-shape" width="764" height="58"><polygon points="0,0 648,0 624,46 0,46" fill="#062e74"/><polygon points="662,0 764,0 764,46 638,46" fill="#9fd3ee"/><polygon points="0,46 406,46 398,58 0,58" fill="#9fd3ee"/></svg>
  <h2 class="slide-title">Your Money</h2>
  <div class="abs label" style="left:35px;top:128px">Objective:</div>
  <ul class="bullets abs" style="left:35px;top:153px">
    <li><svg class="tick" viewBox="0 0 10 10"><circle cx="5" cy="5" r="5" fill="#0f44b0"/><path d="M2.8 5.1l1.5 1.5 3-3" stroke="#fff" stroke-width="1.3" fill="none"/></svg>Build as big as Possible</li>
  </ul>
  <div class="abs label" style="left:35px;top:183px">How:</div>
  <ul class="bullets abs" style="left:35px;top:208px;display:grid;gap:9px">
    <li><svg class="tick" viewBox="0 0 10 10"><circle cx="5" cy="5" r="5" fill="#0f44b0"/><path d="M2.8 5.1l1.5 1.5 3-3" stroke="#fff" stroke-width="1.3" fill="none"/></svg>Higher Rates of returns?</li>
    <li><svg class="tick" viewBox="0 0 10 10"><circle cx="5" cy="5" r="5" fill="#0f44b0"/><path d="M2.8 5.1l1.5 1.5 3-3" stroke="#fff" stroke-width="1.3" fill="none"/></svg>More Risk?</li>
    <li><svg class="tick" viewBox="0 0 10 10"><circle cx="5" cy="5" r="5" fill="#0f44b0"/><path d="M2.8 5.1l1.5 1.5 3-3" stroke="#fff" stroke-width="1.3" fill="none"/></svg>Better products?</li>
  </ul>
  <div class="abs note" style="left:33px;top:285px">Having an efficient Overall Strategy is the key,It All Starts Here!</div>
  <div class="photo" role="img" aria-label="Business team gathered around a laptop in a bright office" style="left:423px;top:112px;width:305px;height:250px;background:linear-gradient(160deg,#e6e9ec,#b9a999 55%,#5b5f66)"></div>
  <footer class="footer"><span class="page">PAGE | 02</span><span class="rights">© 2024 TerraVesta &nbsp;| All Rights Reserved</span><span class="site"><svg width="7" height="7" viewBox="0 0 10 10"><circle cx="5" cy="5" r="5" fill="#062e74"/></svg>www.terravesta.com</span></footer>
</section>

<!-- 03 Your Money -->
<section class="slide col-l row-2">
  <svg class="header-shape" width="764" height="58"><polygon points="0,0 648,0 624,46 0,46" fill="#062e74"/><polygon points="662,0 764,0 764,46 638,46" fill="#9fd3ee"/><polygon points="0,46 406,46 398,58 0,58" fill="#9fd3ee"/></svg>
  <h2 class="slide-title">Your Money</h2>
  <div class="card" style="left:34px"><div class="card-band"></div><div class="photo" role="img" aria-label="Climbing helmet, shoes and rope on rock" style="background:linear-gradient(135deg,#8b6a4c,#c9a27a 50%,#6d5038)"></div><div class="card-title">Equipment and Tools</div><div class="card-sub">Products</div></div>
  <div class="card" style="left:409px"><div class="card-band"></div><div class="photo" role="img" aria-label="Climber scaling a cliff above snowy mountains" style="background:linear-gradient(135deg,#cfe0ec,#8fb2cc 55%,#3e4a55)"></div><div class="card-title">Skill and Technique</div><div class="card-sub">Strategy</div></div>
  <footer class="footer"><span class="page">PAGE | 03</span><span class="rights">© 2024 TerraVesta &nbsp;| All Rights Reserved</span><span class="site"><svg width="7" height="7" viewBox="0 0 10 10"><circle cx="5" cy="5" r="5" fill="#062e74"/></svg>www.terravesta.com</span></footer>
</section>

<!-- 04 Strategy -->
<section class="slide col-r row-2">
  <svg class="header-shape" width="764" height="58"><polygon points="0,0 648,0 624,46 0,46" fill="#062e74"/><polygon points="662,0 764,0 764,46 638,46" fill="#9fd3ee"/><polygon points="0,46 406,46 398,58 0,58" fill="#9fd3ee"/></svg>
  <h2 class="slide-title">Why is your Strategy so Important?</h2>
  <div class="photo" role="img" aria-label="Presenter in a suit briefing colleagues at a boardroom table" style="left:34px;top:132px;width:314px;height:246px;background:linear-gradient(160deg,#eef0f2,#c9ccd1 45%,#6d5b4b 80%,#3b3330)"></div>
  <div class="logo-box"><div class="name"><i></i>TerraVesta</div><div class="region">Northern California</div></div>
  <p class="abs body-copy" style="left:447px;top:121px;width:300px">We all only have a finite amount of Money, We have to Be Efficient With it in the Short Time We have</p>
  <div class="abs emph" style="left:447px;top:170px">In Efficiencies cause major Losses to occur</div>
  <div class="abs label" style="left:448px;top:202px;font-size:10.5px">These Losses can be reflected in:</div>
  <ul class="bullets abs" style="left:448px;top:227px;display:grid;gap:9px">
    <li><svg class="tick" viewBox="0 0 10 10"><circle cx="5" cy="5" r="5" fill="#0f44b0"/><path d="M2.8 5.1l1.5 1.5 3-3" stroke="#fff" stroke-width="1.3" fill="none"/></svg>Lower Current Lifestyle</li>
    <li><svg class="tick" viewBox="0 0 10 10"><circle cx="5" cy="5" r="5" fill="#0f44b0"/><path d="M2.8 5.1l1.5 1.5 3-3" stroke="#fff" stroke-width="1.3" fill="none"/></svg>Lower Retirement Income</li>
    <li><svg class="tick" viewBox="0 0 10 10"><circle cx="5" cy="5" r="5" fill="#0f44b0"/><path d="M2.8 5.1l1.5 1.5 3-3" stroke="#fff" stroke-width="1.3" fill="none"/></svg>inasdequate Protection</li>
    <li><svg class="tick" viewBox="0 0 10 10"><circle cx="5" cy="5" r="5" fill="#0f44b0"/><path d="M2.8 5.1l1.5 1.5 3-3" stroke="#fff" stroke-width="1.3" fill="none"/></svg>Loss of Financial Control</li>
    <li><svg class="tick" viewBox="0 0 10 10"><circle cx="5" cy="5" r="5" fill="#0f44b0"/><path d="M2.8 5.1l1.5 1.5 3-3" stroke="#fff" stroke-width="1.3" fill="none"/></svg>Financial Vulnerablility</li>
    <li><svg class="tick" viewBox="0 0 10 10"><circle cx="5" cy="5" r="5" fill="#0f44b0"/><path d="M2.8 5.1l1.5 1.5 3-3" stroke="#fff" stroke-width="1.3" fill="none"/></svg>Higher Taxes and fees</li>
  </ul>
  <footer class="footer"><span class="page">PAGE | 04</span><span class="rights">© 2024 TerraVesta &nbsp;| All Rights Reserved</span><span class="site"><svg width="7" height="7" viewBox="0 0 10 10"><circle cx="5" cy="5" r="5" fill="#062e74"/></svg>www.terravesta.com</span></footer>
</section>

<!-- 05 Efficiency -->
<section class="slide col-l row-3">
  <svg class="header-shape" width="764" height="58"><polygon points="0,0 648,0 624,46 0,46" fill="#062e74"/><polygon points="662,0 764,0 764,46 638,46" fill="#9fd3ee"/><polygon points="0,46 406,46 398,58 0,58" fill="#9fd3ee"/></svg>
  <h2 class="slide-title">How Significant is Efficiency?</h2>
  <div class="efficiency-copy">
    <p>An individual might be able to create $75,000/Year (1 unit) of retirement income based on Current Savings With an inefficient process.</p>
    <p>The Same Individual Could Create &nbsp;$125,000/Year &nbsp;of Retiement income with an Efficient Process using the Same Amount of Savings.</p>
  </div>
  <div class="photo" role="img" aria-label="Colleagues reviewing sticky notes on a glass wall" style="left:396px;top:98px;width:313px;height:248px;border-radius:12px;background:linear-gradient(120deg,#6f7d7a,#b7a58e 45%,#3d3a3c 85%)"></div>
  <footer class="footer"><span class="page">PAGE | 05</span><span class="rights">© 2024 TerraVesta &nbsp;| All Rights Reserved</span><span class="site"><svg width="7" height="7" viewBox="0 0 10 10"><circle cx="5" cy="5" r="5" fill="#062e74"/></svg>www.terravesta.com</span></footer>
</section>

<!-- 06 Distribution Rates -->
<section class="slide col-r row-3">
  <svg class="header-shape" width="764" height="58"><polygon points="0,0 648,0 624,46 0,46" fill="#062e74"/><polygon points="662,0 764,0 764,46 638,46" fill="#9fd3ee"/><polygon points="0,46 406,46 398,58 0,58" fill="#9fd3ee"/></svg>
  <h2 class="slide-title" style="left:33px">Distribution Rates</h2>
  <div class="abs" style="left:0;top:92px;width:764px;text-align:center;font-size:10.5px">How Could you Do this Without Higher probabilities of Running Out of money?</div>
  <div class="photo" role="img" aria-label="Sketch of money mountains with a $1,000,000 peak and $70,000–$130,000 a year income flowing to a retiree" style="left:104px;top:131px;width:556px;height:237px;border:1px solid #062e74;background:linear-gradient(180deg,#ffffff,#f1f6f3)"></div>
  <footer class="footer"><span class="page">PAGE | 06</span><span class="rights">© 2024 TerraVesta &nbsp;| All Rights Reserved</span><span class="site"><svg width="7" height="7" viewBox="0 0 10 10"><circle cx="5" cy="5" r="5" fill="#062e74"/></svg>www.terravesta.com</span></footer>
</section>

<!-- 07 Hierarchy -->
<section class="slide col-l row-4">
  <svg class="header-shape" width="764" height="58"><polygon points="0,0 648,0 624,46 0,46" fill="#062e74"/><polygon points="662,0 764,0 764,46 638,46" fill="#9fd3ee"/><polygon points="0,46 406,46 398,58 0,58" fill="#9fd3ee"/></svg>
  <h2 class="slide-title" style="left:33px">Retirement Income Strategy Hierarchy</h2>
  <table class="strategy-table">
    <tr><th>Retirement Income Strategies</th><th class="eff">Efficiency</th></tr>
    <tr><td>Two Economic owers Approach: Covered Assets option,Volatility Buffer Option</td><td class="eff" rowspan="4">
      <svg width="110" height="240" viewBox="0 0 110 240" aria-hidden="true"><polygon points="55,40 88,74 69,74 69,190 41,190 41,74 22,74" fill="#062e74"/></svg>
    </td></tr>
    <tr><td>Joint Single premium Immediate Annuity</td></tr>
    <tr><td>Growth Annuity With Income Rider</td></tr>
    <tr><td>One Economic Power Approach Investments Only Using Withdrawal Rate Simulations</td></tr>
  </table>
  <footer class="footer"><span class="page">PAGE | 07</span><span class="rights">© 2024 TerraVesta &nbsp;| All Rights Reserved</span><span class="site"><svg width="7" height="7" viewBox="0 0 10 10"><circle cx="5" cy="5" r="5" fill="#062e74"/></svg>www.terravesta.com</span></footer>
</section>

<!-- 08 Closing -->
<section class="slide closing col-r row-4">
  <div class="photo" role="img" aria-label="Businessman facing a city skyline, tinted blue" style="inset:0;background:linear-gradient(180deg,rgba(20,70,180,.2) 0%,rgba(10,40,120,.1) 55%,rgba(5,30,90,.55) 100%)"></div>
  <div class="thanks">Thank You!</div>
</section>

</body>
</html>
```